Modern Business Card

Modern professional business card with more than just logo and demographic info. Something memorable.

We are a trendy/modern chiropractic group with an emphasis on neurology, hence the minimalist-type brain logo. We want to convey that modern and technical aspect with professionalism and the elite nature of our practice environment.

```html
<!DOCTYPE html>
<html lang="en">
<head>
<meta charset="utf-8">
<title>Meridian Spine — Business Card</title>
<link rel="stylesheet" href="https://fonts.googleapis.com/css2?family=Cinzel:wght@400;700&family=Arimo:wght@400&display=swap">
<style>
  :root {
    --backdrop: #d9dade;
    --brand-blue: #4680c2;
    --ink-black: #0a0a0b;
    --stripe-grey: #5f6064;
    --paper-white: #ffffff;
    --text-dark: #1c1c1e;
    --text-grey: #5a5a5e;
    --text-light: #e6e6e6;
    --text-muted: #bdbdbd;
  }
  * { box-sizing: border-box; margin: 0; padding: 0; }
  html, body { width: 1200px; height: 1015px; overflow: hidden; }
  body {
    background: var(--backdrop);
    position: relative;
    font-family: "Arimo", Arial, sans-serif;
  }
  .card {
    position: absolute;
    width: 580px;
    height: 331px;
    border-radius: 3px;
    overflow: hidden;
    box-shadow: 0 10px 28px rgba(0,0,0,0.25);
  }
  .card-front {
    left: 70px; top: 100px;
    background: var(--brand-blue);
    display: flex; align-items: center; justify-content: center;
  }
  .brand {
    display: flex; align-items: center; gap: 14px;
    font-family: "Cinzel", "Times New Roman", serif;
    font-weight: 400;
  }
  .brand-mark { width: 34px; height: 34px; flex: none; }
  .brand-name { display: flex; flex-direction: column; line-height: 1; }
  .brand-line-main { font-size: 40px; letter-spacing: 2px; }
  .brand-line-sub { font-size: 24px; letter-spacing: 3px; margin-top: 2px; }
  .card-front .brand { color: var(--paper-white); }
  .card-front .brand-mark { background: var(--paper-white); }

  .card-back {
    left: 550px; top: 570px;
    background: var(--paper-white);
  }
  .wave { position: absolute; inset: 0; width: 100%; height: 100%; }
  .card-back .brand {
    position: absolute; left: 36px; top: 62px;
    gap: 12px;
    color: var(--text-dark);
  }
  .card-back .brand-mark { background: var(--brand-blue); width: 28px; height: 28px; }
  .card-back .brand-line-main { font-size: 32px; }
  .card-back .brand-line-sub { font-size: 19px; color: var(--text-grey); }

  .contact {
    position: absolute; right: 26px; top: 74px;
    text-align: right;
    color: var(--text-light);
    font-size: 12.5px;
    line-height: 1.5;
  }
  .contact-name {
    font-family: "Cinzel", "Times New Roman", serif;
    font-weight: 700;
    color: var(--brand-blue);
    font-size: 15px;
    letter-spacing: 0.5px;
    line-height: 1.2;
  }
  .contact-role { margin-bottom: 10px; }
  .contact-line { display: flex; justify-content: flex-end; align-items: center; gap: 6px; }
  .contact-line svg { width: 11px; height: 11px; fill: var(--brand-blue); }
  .contact-address { margin-top: 10px; color: var(--text-muted); }
</style>
</head>
<body>
  <section class="card card-front" aria-label="Card front">
    <div class="brand">
      <span class="brand-mark"></span>
      <span class="brand-name">
        <span class="brand-line-main">MERIDIAN</span>
        <span class="brand-line-sub">SPINE</span>
      </span>
    </div>
  </section>

  <section class="card card-back" aria-label="Card back">
    <svg class="wave" viewBox="0 0 580 331" preserveAspectRatio="none" aria-hidden="true">
      <path transform="translate(0,-28)" d="M0,262 C180,250 260,225 320,150 C365,90 385,40 440,20 L580,14 L580,400 L0,400 Z" fill="var(--brand-blue)"/>
      <path transform="translate(0,-20)" d="M0,262 C180,250 260,225 320,150 C365,90 385,40 440,20 L580,14 L580,400 L0,400 Z" fill="var(--paper-white)"/>
      <path transform="translate(0,-14)" d="M0,262 C180,250 260,225 320,150 C365,90 385,40 440,20 L580,14 L580,400 L0,400 Z" fill="var(--stripe-grey)"/>
      <path d="M0,262 C180,250 260,225 320,150 C365,90 385,40 440,20 L580,14 L580,400 L0,400 Z" fill="var(--ink-black)"/>
    </svg>

    <div class="brand">
      <span class="brand-mark"></span>
      <span class="brand-name">
        <span class="brand-line-main">MERIDIAN</span>
        <span class="brand-line-sub">SPINE</span>
      </span>
    </div>

    <div class="contact">
      <p class="contact-name">DANIEL HARPER</p>
      <p class="contact-role">Managing Director</p>
      <p class="contact-line">044-555 018 273
        <svg viewBox="0 0 12 12"><path d="M2.5 1 L4.5 1 L5.3 3.6 L4 4.6 C4.7 6 5.9 7.3 7.4 8 L8.4 6.7 L11 7.5 L11 9.5 C11 10.4 10.3 11 9.5 11 C5 10.6 1.4 7 1 2.5 C1 1.7 1.6 1 2.5 1 Z"/></svg>
      </p>
      <p class="contact-line">info@meridianspine.com
        <svg viewBox="0 0 12 12"><path d="M1 2.5 H11 V9.5 H1 Z M1.6 3 L6 6.4 L10.4 3" stroke="#0a0a0b" stroke-width="0.8"/></svg>
      </p>
      <p class="contact-line">www.meridianspine.com
        <svg viewBox="0 0 12 12"><circle cx="6" cy="6" r="5"/></svg>
      </p>
      <p class="contact-address">88, Harbor Lane Suite 2<br>45120, Eastvale</p>
    </div>
  </section>
</body>
</html>
```